Calvanto Group Real Estate Company business cards

New business card design, we are generally happy with the basic layout of the existing front of business card, (feel free to change) but require a head shot photo on the back side.

http://www.calvanto.com.au/

Attached logos, and existing business card

------------------------------

Target Market(s)

Real estate

Industry/Entity Type

Real Estate

Contact Information for Business Card

Standard size double sided

Font styles to use
Other font styles liked:
• Futura

Requirements
Must have
• Photo head shot on the back side
Nice to have
• yes
Should not have
• No

```html
<!DOCTYPE html>
<html lang="en">
<head>
<meta charset="utf-8">
<title>Calvanto Group – Business Cards</title>
<link rel="stylesheet" href="https://fonts.googleapis.com/css2?family=Open+Sans:wght@400;600;700&display=swap">
<style>
  :root {
    --backdrop: #4a423d;
    --card-black: #050505;
    --card-glow: #2a2a2a;
    --purple: #3b2a78;
    --orange: #f7941d;
    --white: #ffffff;
    --grey: #a9a9a9;
    --photo-light: #3a3a3a;
    --photo-dark: #161616;
  }
  * { box-sizing: border-box; margin: 0; padding: 0; }
  html, body {
    width: 1200px; height: 844px; overflow: hidden;
    background: var(--backdrop);
    font-family: "Open Sans", Arial, sans-serif;
  }
  .stage {
    position: relative; width: 1200px; height: 844px;
    display: flex; align-items: center; justify-content: center; gap: 40px;
  }
  .card {
    position: relative; width: 520px; height: 318px;
    background: var(--card-black); overflow: hidden;
    box-shadow: 0 14px 30px rgba(0,0,0,0.45);
  }

  /* Back side – head shot and contact details */
  .card-back .band-top {
    position: absolute; top: 0; left: 0; right: 0; height: 16px; background: var(--purple);
  }
  .card-back .band-bottom {
    position: absolute; bottom: 0; left: 0; right: 0; height: 16px; background: var(--orange);
  }
  .headshot {
    position: absolute; top: 46px; left: 44px; width: 170px; height: 226px;
    background: linear-gradient(180deg, var(--photo-light) 0%, var(--photo-dark) 100%);
  }
  .contact {
    position: absolute; top: 56px; left: 250px; width: 230px;
    text-align: center; color: var(--white); line-height: 1.25;
  }
  .contact .person-name { color: var(--orange); font-weight: 700; font-size: 19px; }
  .contact .person-role { font-size: 12px; margin-bottom: 12px; }
  .contact .company { color: var(--orange); font-weight: 700; font-size: 16px; }
  .contact .abn { font-size: 14px; margin-bottom: 22px; }
  .contact .abn strong { font-weight: 700; }
  .contact .phone, .contact .email, .contact .web { font-size: 14px; }
  .contact .phone { margin-bottom: 10px; }

  /* Front side – brand */
  .card-front {
    background: radial-gradient(ellipse 60% 55% at 50% 40%, var(--card-glow) 0%, var(--card-black) 75%);
  }
  .tab { position: absolute; width: 28px; height: 42px; }
  .tab::before {
    content: ""; position: absolute; left: 0; top: 0; bottom: 0; width: 5px; background: var(--white);
  }
  .tab-orange { top: 30px; right: 0; background: var(--orange); }
  .tab-purple { top: 176px; left: 0; background: var(--purple); }
  .tab-purple::before { left: auto; right: 0; }
  .brand {
    position: absolute; top: 100px; left: 0; right: 0; text-align: center;
  }
  .brand .company-name {
    color: var(--white); font-weight: 600; font-size: 40px; line-height: 1;
  }
  .brand .tagline {
    color: var(--grey); font-weight: 600; font-size: 16px; margin-top: 14px;
  }
  .brand .services {
    color: var(--orange); font-weight: 600; font-size: 15px; margin-top: 16px; letter-spacing: 0.5px;
  }
  .brand .services .divider { color: var(--grey); margin: 0 6px; }
</style>
</head>
<body>
<main class="stage">
  <section class="card card-back" aria-label="Business card back">
    <div class="band-top"></div>
    <div class="headshot" role="img" aria-label="Head shot photo of Daniel Tran"></div>
    <div class="contact">
      <p class="person-name">Daniel Tran</p>
      <p class="person-role">Director</p>
      <p class="company">Calvanto Group</p>
      <p class="abn"><strong>ABN:</strong> 41 208 663 175</p>
      <p class="phone">0400 555 218</p>
      <p class="email">daniel.tran@calvanto.com.au</p>
      <p class="web">www.calvanto.com.au</p>
    </div>
    <div class="band-bottom"></div>
  </section>

  <section class="card card-front" aria-label="Business card front">
    <div class="tab tab-orange"></div>
    <div class="tab tab-purple"></div>
    <div class="brand">
      <p class="company-name">Calvanto Group</p>
      <p class="tagline">let us show you property</p>
      <p class="services">BUY<span class="divider">|</span>SELL<span class="divider">|</span>RENT</p>
    </div>
  </section>
</main>
</body>
</html>
```